$5 Quest Website Required

I am looking for someone to develop a website akin to the simplicity of www.boxlantern.example with a video in the center or a tab that permits one to "Accept the Challenge."

Incorporates our logo and is used to promote our "$5 Quest Program."

Please see attachments, but we are igniting entrepreneurial spirit among our nation's youth through this interactive and intensive program!

There should be a way to navigate to other sections of the site including:

About
Why
Request $5 Quest Packet
Success Stories
Partners
Link to Norvik Holdings
Updates

Thanks to all in advance!

Looking forward to working with you!

Good feel of what we are looking for in terms of "feel"

http://www.thebrightripple.example/

Thank you,

RB

Please make note of this website, we are going for a feel that is akin to this and less modern and professional...more abstract and interactive...but of course include space for our video:

Colors, feel, imagery, is great. Keep your formats, but bring on the feel!

Thank you all for your hard work and patience.

Thank you all for your hard work thus far.

Meanwhile, please understand that the $5 Quest is young, youthful, full of challenge and vitality, it is a competition among students from high school and universities.  The websites you have delivered are too corporate, stale, and standard.  I'm looking for something that is fresh, different, like www.thebrightripple.example.

Symbols, cartoonish, but serious, down to business and save the world one $5 bill at a time.  The logo can be used as a theme...the colors, the feel.

Video space for explanation on the $5 Quest front and center.  With leaves, $ signs, colorful colors, etc.

Visual needs to be compelling to Join the Challenge! Although Norvik Holdings and the tree is a parent company; $5 Quest is separate and Norvik Holdings should only be mentioned as a link.

PixelHarbor.example in regard to simplicity; and www.thebrightripple.example in terms of style.

Thank you,

Raphael

Like the designs that have been submitted; we are almost there.

Target Market(s)

Professors, students, teachers, parents and NGO leaders who wish to use our program as a way to inspire leadership/entrepreneurship/fundraise for their causes.

Requirements
Must have
• Place for the video, front and center
Include logo
Forsight for blogging, message, etc.
Nice to have
• Plan "buckets" to include"
Explanation Video
Two pamphlets
Contract
FAQs
Website with Blog, voting, registration, video upload, etc.
Flyer perfected
Parable...symbol of our life
Photos
Stats included
Testimonials
Organizations that have used (TKWLM, North Brook Lodge, Marlowton High)
Sponsors (Open Lantern, Copperleaf Learningfield)
Photos from events

I understand this takes coding and such, but want you to be aware of the long term vision for it!

```html
<!DOCTYPE html>
<html lang="en">
<head>
<meta charset="utf-8">
<title>$5 Quest</title>
<link rel="stylesheet" href="https://fonts.googleapis.com/css2?family=Arimo:wght@400;700&family=Roboto+Condensed:wght@400;500;700&family=Ubuntu:wght@400;500&display=swap">
<style>
  :root {
    --green: #07913a;
    --green-dark: #04772e;
    --green-line: #0aa444;
    --lime: #d7e021;
    --lime-light: #eef36a;
    --slate: #58585a;
    --ink: #222222;
    --white: #ffffff;
    --frame-grey: #dcdcdc;
  }
  * { margin: 0; padding: 0; box-sizing: border-box; }
  html, body { width: 1200px; height: 979px; overflow: hidden; background: var(--white); }
  body { position: relative; font-family: "Arimo", Arial, sans-serif; }

  /* Header */
  .site-header { position: absolute; left: 0; top: 0; width: 1200px; height: 216px; background: var(--white); }
  .utility-nav { position: absolute; top: 0; right: 34px; display: flex; align-items: center; height: 28px;
    font-family: "Roboto Condensed", sans-serif; font-weight: 500; font-size: 17px; letter-spacing: .5px; color: var(--ink); }
  .utility-nav a { color: var(--ink); text-decoration: none; padding: 0 12px; }
  .utility-nav .signin { background: linear-gradient(90deg, #e4e4e4, var(--white) 30%); padding: 4px 14px; }
  .language-btn { background: var(--lime); color: var(--ink); font-size: 14px; font-weight: 700; height: 28px;
    display: flex; align-items: center; gap: 10px; padding: 0 12px; border-radius: 0 0 4px 4px; margin-left: 2px; }
  .language-btn svg { width: 13px; height: 11px; }

  .brand-name { font-family: "Arimo", Arial, sans-serif; font-weight: 400; color: var(--ink); white-space: nowrap; }
  .site-header .brand-name { position: absolute; left: 0; width: 1200px; top: 58px; text-align: center;
    font-size: 72px; line-height: 84px; }

  /* Main navigation */
  .main-nav { position: absolute; left: 0; top: 216px; width: 1200px; height: 60px; background: var(--green);
    border-top: 3px solid var(--green-dark); border-bottom: 3px solid var(--green-dark);
    box-shadow: inset 0 3px 0 var(--green-line), inset 0 -3px 0 var(--green-line); }
  .main-nav ul { list-style: none; display: flex; justify-content: center; align-items: center; height: 100%;
    font-family: "Roboto Condensed", sans-serif; font-weight: 500; font-size: 21px; letter-spacing: .6px; }
  .main-nav li { color: var(--white); display: flex; align-items: center; }
  .main-nav li + li::before { content: ""; width: 5px; height: 5px; border-radius: 50%; background: #0c5f2a;
    margin: 0 24px; box-shadow: 0 1px 0 #2fb35c; }
  .main-nav li.current { color: var(--lime); }

  /* Content area */
  .content { position: absolute; left: 0; top: 276px; width: 1200px; height: 626px; background: var(--slate); }

  .welcome { position: absolute; left: 24px; top: 52px; width: 316px; color: var(--white); }
  .welcome h1 { font-family: "Ubuntu", sans-serif; font-weight: 400; font-size: 21px; letter-spacing: .3px;
    padding-bottom: 10px; border-bottom: 2px dotted #d8d8d8; text-shadow: 0 1px 1px rgba(0,0,0,.5); }
  .welcome h1 span { color: var(--lime); }
  .welcome p { font-size: 14.6px; line-height: 21px; text-align: justify; margin-top: 10px; }
  .welcome p:first-of-type { margin-top: 18px; }

  .video-frame { position: absolute; left: 394px; top: 22px; width: 532px; height: 446px; background: var(--white);
    border: 2px solid #f1eab0; border-radius: 6px; padding: 8px; box-shadow: 0 8px 14px rgba(0,0,0,.12); }
  .video-screen { width: 100%; height: 100%; border: 5px solid var(--frame-grey); border-radius: 4px; position: relative;
    background: radial-gradient(circle at 50% 40%, #f2f8f2 0, #f7faf5 45%, var(--white) 70%); }
  .play-button { position: absolute; left: 168px; top: 84px; width: 174px; height: 174px; }
  .video-label { position: absolute; left: 0; right: 0; top: 292px; text-align: center;
    font-family: "Roboto Condensed", sans-serif; font-weight: 500; font-size: 31px; color: #1e1e1e; letter-spacing: .5px; }

  .testimonials { position: absolute; left: 960px; top: 52px; width: 215px; color: var(--white); }
  .testimonials h2 { font-family: "Ubuntu", sans-serif; font-weight: 400; font-size: 21px; text-align: right;
    padding-right: 9px; text-shadow: 0 1px 1px rgba(0,0,0,.5); }
  .testimonials h2 span { color: var(--lime); }
  .testimonial { position: relative; margin-top: 34px; }
  .testimonial + .testimonial { margin-top: 36px; }
  .testimonial .quote-mark { position: absolute; left: -6px; top: -22px; font-family: Georgia, serif; font-size: 120px;
    line-height: 1; color: #6d6d6f; }
  .testimonial p { position: relative; font-size: 15px; line-height: 19.3px; text-align: justify; width: 170px; margin-left: 23px; }
  .testimonial + .testimonial p { margin-left: 19px; }
  .testimonial cite { display: block; font-style: normal; font-size: 14.6px; text-align: right; color: #111; margin-top: 7px; }

  .challenge-cta { position: absolute; left: 288px; top: 512px; width: 710px; height: 66px; }
  .challenge-cta .rule { position: absolute; top: 32px; height: 0; border-top: 2px dashed #c7cf3a; }
  .challenge-cta .rule.left { left: 0; width: 160px; }
  .challenge-cta .rule.right { right: 0; width: 150px; }
  .challenge-cta .ribbon { position: absolute; left: 156px; top: 0; width: 396px; height: 66px; }
  .challenge-cta .ribbon-text { position: absolute; left: 156px; top: 0; width: 396px; height: 66px; display: flex;
    align-items: center; justify-content: center; font-family: "Roboto Condensed", sans-serif; font-weight: 400;
    font-size: 25px; color: #4a4a3a; letter-spacing: .3px; }

  /* Footer */
  .site-footer { position: absolute; left: 0; top: 902px; width: 1200px; height: 77px; background: var(--white); }
  .site-footer .brand-name { position: absolute; left: 40px; top: 24px; font-size: 24px; line-height: 30px; }
  .footer-nav { position: absolute; right: 40px; top: 22px; display: flex; gap: 22px; font-size: 13.3px; color: var(--ink); }
  .copyright { position: absolute; right: 40px; top: 49px; font-size: 13.3px; color: var(--ink); }
</style>
</head>
<body>

<header class="site-header">
  <nav class="utility-nav">
    <a href="#">FAQ</a>
    <a href="#" class="signin">SIGNIN</a>
    <span class="language-btn">LANGUAGE
      <svg viewBox="0 0 13 11"><path d="M0 0h13L6.5 11z" fill="#222"/></svg>
    </span>
  </nav>
  <span class="brand-name">$5 Quest</span>
</header>

<nav class="main-nav">
  <ul>
    <li class="current">HOME</li>
    <li>ABOUT US</li>
    <li>WHY WE ARE?</li>
    <li>SUCCESS STORIES</li>
    <li>PARTNERS</li>
    <li>NORVIK HOLDINGS</li>
  </ul>
</nav>

<main class="content">
  <section class="welcome">
    <h1>WELCOME TO <span>$5 QUEST</span></h1>
    <p>Lorem ipsum dolor sit amet, consectetur adipiscing elit. Curabitur eu nisl odio. Cras egestas turpis in mi feugiat vel tincidunt arcu accumsan. Phasellus non posuere eros. Aenean consectetur.</p>
    <p>sapien in elit luctus ac posuere purus placerat. Aliquam turpis lorem,.</p>
    <p>Donec fermentum sodales erat, quis consequat nisi ornare eget. Duis volutpat justo ut ante imperdiet feugiat.&nbsp; fermentum sodales erat, quis consequat nisi ornare eget. Duis volutpat justo ut ante imperdiet feugiat.</p>
    <p>sapien in elit luctus ac posuere purus placerat. Aliquam turpis lorem,.</p>
  </section>

  <section class="video-frame">
    <div class="video-screen" role="img" aria-label="Explanation video player with soft leaf backdrop">
      <svg class="play-button" viewBox="0 0 174 174" aria-hidden="true">
        <defs>
          <linearGradient id="playFill" x1="0" y1="0" x2="0" y2="1">
            <stop offset="0" stop-color="#111"/>
            <stop offset="1" stop-color="#3a3a3a"/>
          </linearGradient>
          <linearGradient id="arrowFill" x1="0" y1="0" x2="0" y2="1">
            <stop offset="0" stop-color="#f4f4f4"/>
            <stop offset="1" stop-color="#a9a9a9"/>
          </linearGradient>
        </defs>
        <circle cx="87" cy="87" r="87" fill="url(#playFill)"/>
        <path d="M70 55 L115 87 L70 119 Z" fill="url(#arrowFill)"/>
      </svg>
      <div class="video-label">WATCH VIDEO</div>
    </div>
  </section>

  <aside class="testimonials">
    <h2>Client <span>Testimonials</span></h2>
    <blockquote class="testimonial">
      <span class="quote-mark">&ldquo;</span>
      <p>Lorem ipsum dolor sit amsectetur adipiscing elit. Curabitur eu nisl odio. dolor sit amsectetur u nisl odio.</p>
      <cite>- LOREM IPSUM</cite>
    </blockquote>
    <blockquote class="testimonial">
      <span class="quote-mark">&ldquo;</span>
      <p>Lorem ipsum dolor sit amsectetur adipiscing elit. Curabitur eu nisl odio. dolor sit amsectetur u nisl odio.</p>
      <cite>- LOREM IPSUM</cite>
    </blockquote>
  </aside>

  <div class="challenge-cta">
    <span class="rule left"></span>
    <span class="rule right"></span>
    <svg class="ribbon" viewBox="0 0 396 66" aria-hidden="true">
      <path d="M0 0 H396 L380 33 L396 66 H0 L16 33 Z" fill="#d7e021"/>
      <path d="M10 6 H386 L373 33 L386 60 H10 L23 33 Z" fill="none" stroke="#eef36a" stroke-width="2"/>
    </svg>
    <span class="ribbon-text">ACCEPT THE CHALLENGE</span>
  </div>
</main>

<footer class="site-footer">
  <span class="brand-name">$5 Quest</span>
  <nav class="footer-nav">
    <span>Home</span><span>About Us</span><span>Success Stories</span><span>Partners</span><span>Norvik Holdings</span><span>Terms</span><span>Privacy Policy</span>
  </nav>
  <p class="copyright">All Rights reserved @ $5quest</p>
</footer>

</body>
</html>
```